Business card design for holistic health care clinic

We need a double-sided business card design for our holistic health care clinic that integrates our logo design and also its color scheme. My business is called Valmira. It is an integrative medicine clinic. You have already done the logo for me. Please ensure an elegant and upscale design that is not cluttered, but still has all the necessary information (please see below for details).

Target Market(s)

Wellness, fitness, rehabilitation for educated, well-traveled open-minded clients who are focused on natural, organic, balanced and preventive healthcare and lifestyle.

Industry/Entity Type

Medical

Contact Information for Business Card

Modern, clean.

Number of Pages Required

1 page

Font styles to use
Serif
Sans Serif

Colors

Designer to choose colors to be used in the design.

Requirements
Must have
• Logo on one side, all other information on the other side.
• Other information should include:
• Tobias Wrenfeld - DOE, CPT, LMT
• 4100 East Marrow Drive
• Austin, TX 78119
• 512 555 0148
• 818 555 0192
• info@ValmiraHealth.example
• t.wrenfeld@ValmiraHealth.example
Nice to have
• Darker background on front - but not totally black - shaded/dark gray.

```html
<!DOCTYPE html>
<html lang="en">
<head>
<meta charset="utf-8">
<title>Valmira Business Card</title>
<link rel="stylesheet" href="https://fonts.googleapis.com/css2?family=Nunito:wght@800&family=Roboto:wght@400;500&family=Roboto+Condensed:wght@700&display=swap">
<style>
  :root {
    --page-bg: #e6e1da;
    --card-dark: #2b2b2b;
    --brand-blue: #0b91d1;
    --back-blue: #0a93cf;
    --ink-dark: #242424;
    --ink-light: #ffffff;
  }
  * { margin: 0; padding: 0; box-sizing: border-box; }
  html, body {
    width: 1200px; height: 960px; overflow: hidden;
    background: var(--page-bg);
  }
  .canvas { position: relative; width: 1200px; height: 960px; }
  .card {
    position: absolute; left: 312px; width: 600px; height: 343px; overflow: hidden;
  }
  .card--front { top: 113px; background: var(--card-dark); }
  .card--back { top: 472px; background: var(--back-blue); }

  .edge-band {
    position: absolute; left: 0; top: 0; width: 18px; height: 100%;
    background: var(--brand-blue);
  }

  .brand { position: absolute; text-align: center; white-space: nowrap; }
  .brand__name {
    font-family: "Nunito", sans-serif; font-weight: 800;
    letter-spacing: 1px; line-height: 1;
  }
  .brand__tagline {
    font-family: "Nunito", sans-serif; font-weight: 800; line-height: 1;
  }
  .card--front .brand { right: 40px; top: 82px; color: var(--brand-blue); }
  .card--front .brand__name { font-size: 52px; }
  .card--front .brand__tagline { font-size: 15px; margin-top: 6px; }

  .card--back .brand { left: 0; right: 0; top: 150px; color: var(--ink-dark); }
  .card--back .brand__name { font-size: 62px; }
  .card--back .brand__tagline { font-size: 17px; margin-top: 4px; }

  .person { position: absolute; left: 42px; top: 212px; right: 40px; }
  .person__name {
    font-family: "Roboto Condensed", sans-serif; font-weight: 700;
    font-size: 21px; color: var(--brand-blue); line-height: 1;
  }
  .person__credentials {
    display: flex; align-items: center; gap: 8px; margin-top: 5px;
    font-family: "Roboto Condensed", sans-serif; font-weight: 700;
    font-size: 11px; color: var(--brand-blue);
  }
  .person__credentials::after {
    content: ""; flex: 1; height: 1px; background: var(--brand-blue);
  }

  .contact {
    position: absolute; left: 42px; top: 262px;
    display: flex; font-family: "Roboto", sans-serif; white-space: nowrap;
    font-size: 13px; line-height: 19px; color: var(--ink-light);
  }
  .contact__group { padding-right: 14px; }
  .contact__group:last-child { padding-right: 0; }
  .contact__group + .contact__group {
    border-left: 3px solid var(--brand-blue); padding-left: 12px;
  }
  .contact__label { color: var(--brand-blue); font-weight: 500; }

  .rule {
    position: absolute; left: 42px; right: 40px; top: 315px;
    height: 1px; background: var(--brand-blue);
  }

  .slogan {
    position: absolute; left: 0; right: 0; top: 292px; text-align: center;
    font-family: "Roboto", sans-serif; font-size: 14px; color: var(--ink-dark);
  }
</style>
</head>
<body>
<main class="canvas">
  <section class="card card--front" aria-label="Card front">
    <div class="edge-band"></div>
    <div class="brand">
      <div class="brand__name">VALMIRA</div>
      <div class="brand__tagline">Integrative Holistic Medicine</div>
    </div>
    <div class="person">
      <div class="person__name">TOBIAS WRENFELD</div>
      <div class="person__credentials">DOE, CPT, LMT</div>
    </div>
    <div class="contact">
      <div class="contact__group">
        <div>4100 East Marrow Drive</div>
        <div>Austin, TX 78119</div>
      </div>
      <div class="contact__group">
        <div><span class="contact__label">P:</span> 512 555 0148</div>
        <div><span class="contact__label">C:</span> 818 555 0192</div>
      </div>
      <div class="contact__group">
        <div>t.wrenfeld@ValmiraHealth.example</div>
        <div>www.ValmiraHealth.example</div>
      </div>
    </div>
    <div class="rule"></div>
  </section>

  <section class="card card--back" aria-label="Card back">
    <div class="brand">
      <div class="brand__name">VALMIRA</div>
      <div class="brand__tagline">Integrative Holistic Medicine</div>
    </div>
    <p class="slogan">it’s all about you — your health, your objectives</p>
  </section>
</main>
</body>
</html>
```